Business Card Design for Technology Company

New business card design needed for technology company director.
Ideally, the design will fit the style and nature of the industry. We are a supplier of quality products and services, and we hope the design will give customers and suppliers this impression.

Target Market(s)

3D Printing Industry

Industry/Entity Type

Technology Equipment

Contact Information for Business Card

Name: Marcus Lin
Title: Director
Company address: Factory K4, 7B Harlowe Road, Springvale Victoria Australia 3150
Telephone: +61-3-8555 6413
Email: marcus.lin@vortalmake.com.au
Website: www.vortalmake.com.au

Requirements
Must have
• All information in business card details
• Company logo
• '3D Printers and 3D Print Filaments' at proper place
Nice to have
• Style to fit the industry
• Colour to fit logo

```html
<!DOCTYPE html>
<html lang="en">
<head>
<meta charset="utf-8">
<title>Vortal Make – Business Card</title>
<link rel="stylesheet" href="https://fonts.googleapis.com/css2?family=Lato:wght@400;700&display=swap">
<style>
  :root {
    --backdrop: #222222;
    --card: #ffffff;
    --ink: #2b2b2b;
    --ink-soft: #444444;
    --orange: #f39a2b;
    --blue: #2394d6;
    --divider: #c8c8c8;
  }
  * { margin: 0; padding: 0; box-sizing: border-box; }
  html, body {
    width: 1200px; height: 900px; overflow: hidden;
    background: var(--backdrop);
    font-family: "Lato", Arial, sans-serif;
  }
  .canvas { position: relative; width: 1200px; height: 900px; }

  .card {
    position: absolute;
    width: 620px; height: 354px;
    left: 290px;
    background: var(--card);
    overflow: hidden;
  }
  .card--front { top: 70px; }
  .card--back { top: 476px; }

  /* Front */
  .front-mark {
    position: absolute; left: 300px; top: 112px;
    width: 130px; height: 130px;
    background: var(--orange);
  }
  .front-divider {
    position: absolute; left: 470px; top: 112px;
    width: 2px; height: 130px;
    background: var(--divider);
  }
  .front-lockup {
    position: absolute;
    left: 400px; top: 146px;
    width: 310px; height: 62px;
    transform: rotate(-90deg);
    transform-origin: center center;
    text-align: center;
  }
  .front-lockup__name {
    font-weight: 700; font-size: 36px; letter-spacing: 6px;
    line-height: 40px; color: var(--ink); white-space: nowrap;
  }
  .front-lockup__tagline {
    font-weight: 700; font-size: 10px; letter-spacing: 2px;
    line-height: 18px; color: var(--ink); white-space: nowrap;
  }

  /* Back */
  .brand {
    position: absolute; left: 90px; top: 44px;
    display: flex; align-items: center; gap: 12px;
  }
  .brand__square { width: 40px; height: 40px; background: var(--orange); flex: none; }
  .brand__name {
    font-weight: 700; font-size: 26px; letter-spacing: 4px;
    line-height: 28px; color: var(--ink); white-space: nowrap;
  }
  .brand__tagline {
    font-weight: 700; font-size: 8px; letter-spacing: 1.6px;
    line-height: 12px; color: var(--ink); white-space: nowrap;
  }

  .rule { position: absolute; height: 4px; }
  .rule--orange { left: 0; top: 166px; width: 300px; background: var(--orange); }
  .rule--blue { left: 500px; top: 170px; width: 120px; background: var(--blue); }

  .person { position: absolute; left: 310px; top: 152px; width: 180px; text-align: center; }
  .person__name { font-size: 24px; line-height: 28px; color: var(--ink-soft); letter-spacing: 1px; white-space: nowrap; }
  .person__title { font-size: 13px; font-weight: 700; color: var(--orange); letter-spacing: 1px; }

  .contacts { position: absolute; left: 46px; top: 198px; list-style: none; }
  .contacts li {
    display: flex; align-items: center; gap: 10px;
    font-size: 14px; color: var(--ink-soft); line-height: 23px; white-space: nowrap;
  }
  .contacts svg { width: 13px; height: 13px; flex: none; }
  .address { position: absolute; left: 40px; top: 274px; font-size: 14px; line-height: 21px; color: var(--ink-soft); }

  .social { position: absolute; left: 400px; top: 296px; display: flex; gap: 24px; }
  .social__item { width: 18px; height: 18px; background: var(--blue); border-radius: 3px; }
</style>
</head>
<body>
<main class="canvas">
  <section class="card card--front" aria-label="Card front">
    <div class="front-mark"></div>
    <div class="front-divider"></div>
    <div class="front-lockup">
      <p class="front-lockup__name">VORTAL MAKE</p>
      <p class="front-lockup__tagline">3D PRINTERS AND 3D PRINT FILAMENTS</p>
    </div>
  </section>

  <section class="card card--back" aria-label="Card back">
    <div class="brand">
      <span class="brand__square"></span>
      <div>
        <p class="brand__name">VORTAL MAKE</p>
        <p class="brand__tagline">3D PRINTERS AND 3D PRINT FILAMENTS</p>
      </div>
    </div>

    <div class="rule rule--orange"></div>
    <div class="person">
      <p class="person__name">MARCUS LIN</p>
      <p class="person__title">DIRECTOR</p>
    </div>
    <div class="rule rule--blue"></div>

    <ul class="contacts">
      <li>
        <svg viewBox="0 0 24 24" aria-hidden="true"><path fill="#2394d6" d="M6.6 10.8a15 15 0 0 0 6.6 6.6l2.2-2.2c.3-.3.7-.4 1-.2 1.1.4 2.3.6 3.6.6.6 0 1 .4 1 1V20c0 .6-.4 1-1 1A17 17 0 0 1 3 4c0-.6.4-1 1-1h3.5c.6 0 1 .4 1 1 0 1.3.2 2.5.6 3.6.1.3 0 .7-.2 1z"/></svg>
        +61-3-8555 6413
      </li>
      <li>
        <svg viewBox="0 0 24 24" aria-hidden="true"><rect x="2" y="5" width="20" height="14" fill="none" stroke="#2394d6" stroke-width="2"/><path d="M2 5l10 8 10-8" fill="none" stroke="#2394d6" stroke-width="2"/></svg>
        marcus.lin@vortalmake.com.au
      </li>
      <li>
        <svg viewBox="0 0 24 24" aria-hidden="true"><g fill="none" stroke="#2394d6" stroke-width="2"><circle cx="12" cy="12" r="10"/><ellipse cx="12" cy="12" rx="4" ry="10"/><path d="M2 12h20"/></g></svg>
        www.vortalmake.com.au
      </li>
    </ul>
    <p class="address">Factory K4, 7B Harlowe Road,<br>Springvale Victoria Australia 3150</p>

    <div class="social" role="img" aria-label="Social media links">
      <span class="social__item"></span>
      <span class="social__item"></span>
      <span class="social__item"></span>
    </div>
  </section>
</main>
</body>
</html>
```